Inspiring Fundraising Foundation Website to Provide Academic Scholarships

Hello, we are launching a foundation to provide academic scholarships to high school students for college. We'd like this to be an informational website with contact information. There will be a total of approximately 5-7 pages in all.
The color scheme will be purple and white, with a girly feel. I 've attached the logo for reference!

Target Market(s)

high school students, college students

Industry/Entity Type

Education

Coding

Coded - Design and coding required

Number of Pages Required

5+ page

Font styles to use
Serif
Sans Serif
Script

Colors
6b449b
886aae
b7a5cd
e4daeb
ffffff
fdf9cf
fbf289

Requirements
Must have
• Purple, girly feel, to reflect the logo's style. Should be light-themed
Should not have
• No dark themes (aka heavy on black or dark colors)

```html
<!DOCTYPE html>
<html lang="en">
<head>
<meta charset="utf-8">
<title>Lorena Vidal Foundation</title>
<link href="https://fonts.googleapis.com/css2?family=Satisfy&family=Open+Sans:ital,wght@0,300;0,400;0,600;0,700;1,400&display=block" rel="stylesheet">
<style>
:root{
  --purple-deep:#6b449b;
  --purple:#886aae;
  --purple-soft:#b7a5cd;
  --purple-pale:#e4daeb;
  --white:#ffffff;
  --cream:#fdf9cf;
  --ink:#333333;
  --muted:#7a7a7a;
  --line:#e2e2e2;
}
*{box-sizing:border-box;margin:0;padding:0}
html,body{width:1200px;height:3000px;overflow:hidden}
body{position:relative;background:var(--white);font-family:"Open Sans",Arial,sans-serif;color:var(--ink)}
.abs{position:absolute}

/* top bar */
.topbar{left:0;top:0;width:1200px;height:32px;background:var(--purple);color:var(--white);font-size:10px;letter-spacing:.3px}
.topbar .item{position:absolute;top:0;line-height:32px;display:flex;align-items:center;gap:6px}
.topbar svg{width:11px;height:11px;fill:var(--white)}

/* header */
.header{left:0;top:32px;width:1200px;height:100px;background:var(--white)}
.brand-plate{left:200px;top:32px;width:200px;height:196px;z-index:3}
.brand{left:200px;top:58px;width:200px;text-align:center;z-index:4;color:var(--purple-deep);font-weight:700;font-size:24px;line-height:26px}
.brand .mark{display:block;width:22px;height:22px;border-radius:50%;background:var(--purple-deep);margin:0 auto 6px}
.brand small{display:block;font-size:13px;line-height:18px;letter-spacing:2px;font-weight:700}
.nav{left:434px;top:64px;height:38px;display:flex;align-items:center;font-size:12.5px;color:var(--ink)}
.nav a{color:inherit;text-decoration:none;padding:0 18px;line-height:38px;display:block}
.nav a.active{background:var(--purple-deep);color:var(--white);margin-right:18px;padding:0 16px}
.search{left:1048px;top:72px;width:20px;height:20px}

/* hero */
.hero{left:0;top:132px;width:1200px;height:514px;background:linear-gradient(100deg,#b7c7d8 0%,#e6dcd2 30%,#f2d8c4 50%,#dfe4ec 72%,#9fb5cf 100%)}
.hero-title{left:128px;top:276px;font-family:"Satisfy","Segoe Script","Brush Script MT",cursive;font-weight:400;color:var(--white);font-size:78px;line-height:96px;text-shadow:0 2px 8px rgba(0,0,0,.25)}
.btn{display:inline-block;background:var(--purple-deep);color:var(--white);font-weight:700;font-size:12px;letter-spacing:.4px;text-align:center}
.hero-btn{left:132px;top:510px;width:168px;height:40px;line-height:40px;font-size:13px}

/* section titles */
.rule{width:88px;height:3px;background:var(--purple-deep)}
.sec-title{width:1200px;left:0;text-align:center;font-size:27px;font-weight:400;color:#2e2e2e}

/* welcome */
.video{left:134px;top:816px;width:392px;height:234px;background:linear-gradient(135deg,#c9a27e,#8c6f62 45%,#b84a3f 70%,#6c5e68)}
.play{left:304px;top:907px;width:52px;height:52px}
.welcome-text{left:576px;top:814px;width:494px;font-size:11.5px;line-height:22px;color:var(--muted)}
.welcome-text p+p{margin-top:14px}
.welcome-btn{left:576px;top:1008px;width:110px;height:42px;line-height:42px;font-size:11px}

/* how it works */
.works{left:0;top:1138px;width:1200px;height:520px;background:var(--cream)}
.cards{left:132px;top:1362px;width:936px;height:206px;background:var(--white);border:1px solid #ece5b8;display:flex}
.card{flex:1;border-right:1px solid #ece5b8;text-align:center;position:relative}
.card:last-child{border-right:0}
.card .icon{position:absolute;left:50%;top:-48px;margin-left:-48px;width:96px;height:96px;border-radius:50%;background:var(--purple-deep);display:flex;align-items:center;justify-content:center}
.card .icon svg{width:46px;height:46px;stroke:var(--white);fill:none;stroke-width:2;stroke-linecap:round;stroke-linejoin:round}
.card h3{margin-top:66px;font-size:14px;font-weight:400;color:#2e2e2e}
.card p{margin:12px auto 0;width:180px;font-size:11px;line-height:20px;color:var(--muted)}
.card .more{display:block;margin-top:12px;font-size:10.5px;font-weight:700;color:var(--purple-deep)}

/* about */
.about{left:0;top:1658px;width:1200px;height:342px;background:linear-gradient(90deg,#17151b,#2a2630 45%,#1f1c23)}
.portrait{left:132px;top:1724px;width:212px;height:212px;border-radius:50%;border:5px solid var(--white);background:linear-gradient(160deg,#d9c9c2,#a45a52 60%,#6e3a3a)}
.about-title{left:430px;top:1742px;font-size:27px;color:var(--white);font-weight:400}
.about-text{left:430px;top:1794px;width:650px;font-size:11.5px;line-height:23px;color:var(--white)}
.about-btn{left:430px;top:1888px;width:110px;height:40px;line-height:40px;font-size:11px}

/* scholarships */
.scholar{top:2170px;width:298px}
.scholar .label{font-size:10px;font-weight:700;color:var(--purple-deep)}
.scholar .photo{margin-top:10px;height:162px}
.scholar h4{margin-top:20px;font-size:14.5px;font-weight:400;color:#2e2e2e}
.scholar p{margin-top:8px;font-size:11px;line-height:19px;color:var(--muted);padding-bottom:16px;border-bottom:1px solid var(--line)}

/* testimonial */
.quote-band{left:0;top:2556px;width:1200px;height:218px;background:var(--purple)}
.quote-face{left:160px;top:2606px;width:118px;height:118px;border-radius:50%;border:4px solid var(--white);background:linear-gradient(160deg,#e6cdb9,#8f5a48 60%,#4a8f86)}
.quote-rule{left:310px;top:2608px;width:1px;height:116px;background:rgba(255,255,255,.6)}
.quote-text{left:344px;top:2608px;width:680px;font-style:italic;font-size:13px;line-height:27px;color:var(--white)}
.quote-name{left:344px;top:2700px;font-size:11px;font-weight:700;color:var(--white)}
.arrow{width:20px;height:40px;top:2644px}

/* footer */
.foot-head{top:2820px;font-size:14px;font-weight:600;color:#2e2e2e;letter-spacing:.3px}
.foot-line{font-size:11px;color:#555;display:flex;align-items:center;gap:10px;line-height:18px}
.foot-line svg{width:13px;height:13px;fill:var(--purple-deep);flex:none}
.foot-divider{top:2816px;width:1px;height:110px;background:var(--line)}
.news-input{left:564px;top:2856px;width:198px;height:38px;border:1px solid var(--line);font-size:11px;color:#777;padding-left:12px;line-height:36px}
.news-btn{left:768px;top:2856px;width:86px;height:38px;line-height:38px;font-size:10.5px}
.social{top:2856px;width:38px;height:38px;border-radius:50%;border:1.5px solid #555}
.copyright{left:0;top:2944px;width:1200px;height:56px;border-top:1px solid var(--line);text-align:center;line-height:46px;font-size:11px;color:#777}
</style>
</head>
<body>

<!-- top bar -->
<div class="abs topbar">
  <div class="item" style="left:132px">
    <svg viewBox="0 0 24 24"><path d="M6.6 10.8c1.4 2.8 3.8 5.1 6.6 6.6l2.2-2.2c.3-.3.7-.4 1-.2 1.1.4 2.3.6 3.6.6.6 0 1 .4 1 1V20c0 .6-.4 1-1 1C10.6 21 3 13.4 3 4c0-.6.4-1 1-1h3.5c.6 0 1 .4 1 1 0 1.3.2 2.5.6 3.6.1.3 0 .7-.2 1L6.6 10.8z"/></svg>
    PHONE : (+345) 555-0192
  </div>
  <div class="item" style="left:284px">
    <svg viewBox="0 0 24 24"><path d="M2 5h20v14H2z M4 7l8 6 8-6"/></svg>
    EMAIL : INFO@LORENAVIDALFOUNDATION.COM
  </div>
  <div class="item" style="left:936px">
    <svg viewBox="0 0 24 24"><path d="M6 10h12v11H6z M8 10V7a4 4 0 0 1 8 0v3h-2V7a2 2 0 0 0-4 0v3z"/></svg>
    LOG IN
  </div>
  <div class="item" style="left:1010px">
    <svg viewBox="0 0 24 24"><path d="M3 17.2V21h3.8L17.8 10 14 6.2 3 17.2zM20.7 7.1c.4-.4.4-1 0-1.4l-2.4-2.4c-.4-.4-1-.4-1.4 0l-1.8 1.8 3.8 3.8 1.8-1.8z"/></svg>
    REGISTER
  </div>
</div>

<!-- header -->
<header class="abs header"></header>
<svg class="abs brand-plate" viewBox="0 0 200 196" aria-hidden="true"><polygon points="0,0 200,0 200,100 100,196 0,100" fill="#ffffff"/></svg>
<div class="abs brand"><span class="mark"></span>Lorena<br>Vidal<small>FOUNDATION</small></div>

<nav class="abs nav">
  <a class="active">HOME</a>
  <a>ABOUT US</a>
  <a>HOW IT WORKS</a>
  <a>FIND FUNDING</a>
  <a>BLOG</a>
  <a>CONTACT US</a>
</nav>
<svg class="abs search" viewBox="0 0 24 24" fill="none" stroke="#444" stroke-width="2"><circle cx="10" cy="10" r="7"/><path d="M15 15l6 6"/></svg>

<!-- hero -->
<section class="abs hero" role="img" aria-label="Photo of two smiling schoolgirls at a classroom desk with coloured pencils"></section>
<h1 class="abs hero-title">Fundraising<br>Foundation</h1>
<a class="abs btn hero-btn">START A FUNDRAISER</a>

<!-- welcome -->
<div class="abs rule" style="left:556px;top:734px"></div>
<h2 class="abs sec-title" style="top:746px">Welcome to Lorena Vidal Foundation</h2>
<div class="abs video" role="img" aria-label="Video still of children working together in a busy classroom"></div>
<svg class="abs play" viewBox="0 0 52 52"><circle cx="26" cy="26" r="23" fill="rgba(0,0,0,.35)" stroke="#fff" stroke-width="3"/><polygon points="21,16 37,26 21,36" fill="#fff"/></svg>
<div class="abs welcome-text">
  <p>Adipisci velit, sed quia non numquam eius modi tempora incidunt ut labore et dolore magnam aliquam quaerat voluptatem. Ut enim ad minima veniam, quis nostrum...</p>
  <p>Expedita distinctio. Nam libero tempore, cum soluta nobis est eligendi optio cumque nihil impedit quo minus id quod maxime placeat facere possimus, omnis voluptas assumenda est, omnis dolor repellendus. Temporibus autem quibusdam et aut officiis debitis aut rerum necessitatibus saepe eveniet ut et voluptates repudiandae...</p>
</div>
<a class="abs btn welcome-btn">READ MORE &gt;&gt;</a>

<!-- how it works -->
<section class="abs works"></section>
<div class="abs rule" style="left:556px;top:1226px"></div>
<h2 class="abs sec-title" style="top:1238px">How It Works</h2>
<div class="abs cards">
  <div class="card">
    <div class="icon"><svg viewBox="0 0 48 48"><ellipse cx="24" cy="27" rx="15" ry="11"/><circle cx="24" cy="12" r="5"/><path d="M24 10v4M16 37v4M32 37v4M39 25h3"/></svg></div>
    <h3>Deserunt Mollitia</h3>
    <p>Assumenda est, omnis repellendus. Temporibus autem quibusdam officiis debitis...</p>
    <span class="more">READ MORE &gt;&gt;</span>
  </div>
  <div class="card">
    <div class="icon"><svg viewBox="0 0 48 48"><path d="M6 14l18-8 18 8-18 8z"/><path d="M14 18v8c0 4 20 4 20 0v-8"/><path d="M12 42c2-8 22-8 24 0"/></svg></div>
    <h3>Tempor Incididunt</h3>
    <p>Assumenda est, omnis repellendus. Temporibus autem quibusdam officiis debitis...</p>
    <span class="more">READ MORE &gt;&gt;</span>
  </div>
  <div class="card">
    <div class="icon"><svg viewBox="0 0 48 48"><path d="M12 14l12-6 12 6-12 6z"/><path d="M18 17v5c0 3 12 3 12 0v-5"/><path d="M4 34h10l8 4h12l8-6-4-2-8 4h-8"/></svg></div>
    <h3>Fugiat Nulla Pariatur</h3>
    <p>Assumenda est, omnis repellendus. Temporibus autem quibusdam officiis debitis...</p>
    <span class="more">READ MORE &gt;&gt;</span>
  </div>
  <div class="card">
    <div class="icon"><svg viewBox="0 0 48 48"><path d="M24 12c-5-3-12-4-18-3v28c6-1 13 0 18 3 5-3 12-4 18-3V9c-6-1-13 0-18 3z"/><path d="M24 12v28"/></svg></div>
    <h3>Esse Cillum Dolore</h3>
    <p>Assumenda est, omnis repellendus. Temporibus autem quibusdam officiis debitis...</p>
    <span class="more">READ MORE &gt;&gt;</span>
  </div>
</div>

<!-- about -->
<section class="abs about" role="img" aria-label="Dimmed photo of students raising hands in a classroom"></section>
<div class="abs portrait" role="img" aria-label="Portrait of Lorena Vidal seated on a red chair"></div>
<div class="abs rule" style="left:430px;top:1728px;width:86px"></div>
<h2 class="abs about-title">About Lorena Vidal</h2>
<p class="abs about-text">We are excited to announce the Lorena Vidal Foundation in honor of a fabulous angel. We hope to impact the lives of individuals in the same way her dynamic spirit impacted ours. Lorena, we love you and miss you everyday, and through this foundation your name will live on.</p>
<a class="abs btn about-btn">READ MORE &gt;&gt;</a>

<!-- scholarships -->
<div class="abs rule" style="left:556px;top:2092px"></div>
<h2 class="abs sec-title" style="top:2104px">Academic Scholarships</h2>
<article class="abs scholar" style="left:132px">
  <div class="label">ACADEMIC YEAR : 2014-15</div>
  <div class="photo" role="img" aria-label="Photo of students writing at classroom desks" style="background:linear-gradient(135deg,#9bb7d2,#d8c3a8 50%,#6f8fb5)"></div>
  <h4>Modi tempora incidunt ut labore ...</h4>
  <p>Duis aute irure dolor in reprehenderit in voluptate velit esse cillum dolore eu fugiat nulla pariatur...</p>
</article>
<article class="abs scholar" style="left:451px">
  <div class="label">ACADEMIC YEAR : 2015-16</div>
  <div class="photo" role="img" aria-label="Photo of a group of smiling teenage students" style="background:linear-gradient(135deg,#e2a24f,#d9b9a0 45%,#c8602f)"></div>
  <h4>Modi tempora incidunt ut labore ...</h4>
  <p>Duis aute irure dolor in reprehenderit in voluptate velit esse cillum dolore eu fugiat nulla pariatur...</p>
</article>
<article class="abs scholar" style="left:770px">
  <div class="label">ACADEMIC YEAR : 2016-17</div>
  <div class="photo" role="img" aria-label="Photo of high school students standing together with books" style="background:linear-gradient(135deg,#7a8f9c,#d6c0ad 50%,#4f5d6b)"></div>
  <h4>Modi tempora incidunt ut labore ...</h4>
  <p>Duis aute irure dolor in reprehenderit in voluptate velit esse cillum dolore eu fugiat nulla pariatur...</p>
</article>

<!-- testimonial -->
<section class="abs quote-band"></section>
<svg class="abs arrow" style="left:98px" viewBox="0 0 20 40" fill="none" stroke="#fff" stroke-width="2"><path d="M16 4L4 20l12 16"/></svg>
<svg class="abs arrow" style="left:1082px" viewBox="0 0 20 40" fill="none" stroke="#fff" stroke-width="2"><path d="M4 4l12 16L4 36"/></svg>
<div class="abs quote-face" role="img" aria-label="Portrait of a smiling student"></div>
<div class="abs quote-rule"></div>
<p class="abs quote-text">Accusantium doloremque laudantium, totam rem aperiam, eaque ipsa quae ab illo inventore veritatis et quasi architecto beatae vitae dicta sunt explicabo. Nemo enim ipsam voluptatem quia voluptas sit aspernatur aut odit aut fugit, sed quia consequuntur magni dolores...</p>
<div class="abs quote-name">-MARISA KEENE</div>

<!-- footer -->
<h5 class="abs foot-head" style="left:132px">CONTACT US</h5>
<div class="abs foot-line" style="left:132px;top:2852px;width:150px;align-items:flex-start">
  <svg viewBox="0 0 24 24"><path d="M12 2a7 7 0 0 0-7 7c0 5 7 13 7 13s7-8 7-13a7 7 0 0 0-7-7zm0 9.5A2.5 2.5 0 1 1 12 6.5a2.5 2.5 0 0 1 0 5z"/></svg>
  <span># lorem ipsum Dummy<br>Text mcg lorem</span>
</div>
<div class="abs foot-line" style="left:302px;top:2852px">
  <svg viewBox="0 0 24 24"><path d="M6.6 10.8c1.4 2.8 3.8 5.1 6.6 6.6l2.2-2.2c.3-.3.7-.4 1-.2 1.1.4 2.3.6 3.6.6.6 0 1 .4 1 1V20c0 .6-.4 1-1 1C10.6 21 3 13.4 3 4c0-.6.4-1 1-1h3.5c.6 0 1 .4 1 1 0 1.3.2 2.5.6 3.6.1.3 0 .7-.2 1L6.6 10.8z"/></svg>
  Phone : (+345) 555-0192
</div>
<div class="abs foot-line" style="left:302px;top:2876px">
  <svg viewBox="0 0 24 24"><path d="M2 5h20v14H2zm2 2v1l8 5 8-5V7z"/></svg>
  info@lorenavidalfoundation.com
</div>
<div class="abs foot-divider" style="left:536px"></div>
<h5 class="abs foot-head" style="left:564px">NEWSLETTER</h5>
<div class="abs news-input">Email</div>
<a class="abs btn news-btn">SUBSCRIBE</a>
<div class="abs foot-divider" style="left:880px"></div>
<h5 class="abs foot-head" style="left:908px">FOLLOW US</h5>
<div class="abs social" style="left:904px"></div>
<div class="abs social" style="left:950px"></div>
<div class="abs social" style="left:996px"></div>
<div class="abs social" style="left:1042px"></div>
<div class="abs copyright">Copyright © 2017 lorenavidalfoundation.all rights are reserved</div>

</body>
</html>
```